RWT Fittings Ltd Business Cards

We need a business card with our business logo. We provide window and door installations on high-rises in west coast British Colombia, Canada.

I would like my business information and details on one side of the card, and the other side the company name with logo

Target Market(s)

General Contractors

Industry/Entity Type

Construction

Contact Information for Business Card

one side i want my company name and logo in the dark theme logo that i provided

Requirements
Must have
• Marco Peltieri, 16045518293, RWTFittings@mailbox-demo.com, 1407-5194 Linden Row Burnaby BC, V5H 2K9, Owner & Manager

```html
<!DOCTYPE html>
<html lang="en">
<head>
<meta charset="utf-8">
<title>RWT Fittings Ltd — Business Cards</title>
<link rel="stylesheet" href="https://fonts.googleapis.com/css2?family=Roboto:wght@400;500;700;900&display=swap">
<style>
  :root {
    --stage: #242424;
    --card: #1f2024;
    --blue: #29a8e2;
    --grey: #a6a6a6;
    --white: #f2f2f2;
    --rule: #d9d9d9;
    --photo-dark: #2a2624;
    --photo-mid: #4a4440;
  }
  * { box-sizing: border-box; margin: 0; padding: 0; }
  html, body {
    width: 1200px; height: 780px; overflow: hidden;
    background: var(--stage);
    font-family: "Roboto", Arial, sans-serif;
  }
  .stage {
    position: relative; width: 1200px; height: 780px;
    display: flex; flex-direction: column; align-items: center; justify-content: center; gap: 22px;
  }
  .card {
    position: relative; width: 610px; height: 349px; overflow: hidden;
    box-shadow: 0 10px 28px rgba(0,0,0,.45);
  }
  /* Front side */
  .card--front { background: var(--card); }
  .accent-bar { position: absolute; width: 13px; background: var(--blue); }
  .accent-bar--left { left: 26px; top: 160px; height: 160px; }
  .accent-bar--right { right: 26px; top: 22px; height: 150px; }
  .brand {
    position: absolute; display: flex; align-items: center; gap: 10px;
    color: var(--blue); font-weight: 700; white-space: nowrap;
  }
  .brand__mark { background: var(--blue); flex: none; }
  .card--front .brand { left: 62px; top: 128px; font-size: 25px; }
  .card--front .brand__mark { width: 26px; height: 26px; }
  .divider {
    position: absolute; left: 300px; top: 62px; width: 1px; height: 168px;
    background: linear-gradient(to bottom, transparent, var(--rule) 30%, var(--rule) 70%, transparent);
  }
  .contact { position: absolute; left: 332px; top: 70px; color: var(--white); }
  .contact__name { font-size: 27px; font-weight: 900; letter-spacing: -.2px; line-height: 1; }
  .contact__first { color: var(--blue); }
  .contact__last { color: var(--grey); }
  .contact__role { font-size: 13px; font-weight: 500; margin-top: 4px; }
  .contact__list { list-style: none; margin-top: 20px; font-size: 13px; line-height: 1.55; }
  .contact__list li { display: flex; align-items: center; gap: 9px; }
  .contact__list svg { width: 13px; height: 13px; flex: none; }
  .address {
    position: absolute; left: 0; right: 0; bottom: 42px; text-align: center;
    color: var(--white); font-size: 14.5px; letter-spacing: .2px;
  }
  /* Back side */
  .card--back { display: flex; align-items: center; justify-content: center; }
  .backdrop {
    position: absolute; inset: 0;
    background: radial-gradient(ellipse at 60% 40%, var(--photo-mid), var(--photo-dark) 75%);
  }
  .card--back .brand { position: relative; font-size: 40px; gap: 14px; }
  .card--back .brand__mark { width: 40px; height: 40px; }
</style>
</head>
<body>
<main class="stage">
  <section class="card card--front" aria-label="Business card, contact side">
    <span class="accent-bar accent-bar--left"></span>
    <span class="accent-bar accent-bar--right"></span>
    <div class="brand"><span class="brand__mark"></span>RWT Fittings Ltd</div>
    <span class="divider"></span>
    <div class="contact">
      <p class="contact__name"><span class="contact__first">Marco</span> <span class="contact__last">Peltieri</span></p>
      <p class="contact__role">Owner &amp; Manager</p>
      <ul class="contact__list">
        <li>
          <svg viewBox="0 0 24 24" aria-hidden="true"><path fill="var(--blue)" d="M6.6 10.8a15.1 15.1 0 0 0 6.6 6.6l2.2-2.2a1 1 0 0 1 1-.25 11.4 11.4 0 0 0 3.6.57 1 1 0 0 1 1 1V20a1 1 0 0 1-1 1A17 17 0 0 1 3 4a1 1 0 0 1 1-1h3.5a1 1 0 0 1 1 1c0 1.25.2 2.45.57 3.57a1 1 0 0 1-.25 1z"/></svg>
          1604 551 8293
        </li>
        <li>
          <svg viewBox="0 0 24 24" aria-hidden="true"><path fill="var(--blue)" d="M3 5h18a1 1 0 0 1 1 1v12a1 1 0 0 1-1 1H3a1 1 0 0 1-1-1V6a1 1 0 0 1 1-1zm1 2.2V17h16V7.2l-8 5.3z"/></svg>
          RWTFittings@mailbox-demo.com
        </li>
      </ul>
    </div>
    <p class="address">1407-5194 Linden Row Burnaby BC, V5H 2K9</p>
  </section>

  <section class="card card--back" aria-label="Business card, brand side">
    <div class="backdrop" role="img" aria-label="Soft-focus photograph of a dim office interior with a plant"></div>
    <div class="brand"><span class="brand__mark"></span>RWT Fittings Ltd</div>
  </section>
</main>
</body>
</html>
```